The Wardrobe Sage needs a pricing flyer

Single page flyer for The Wardrobe Sage.
The Wardrobe Sage is a lead generation service exclusively for the custom closet industry.
You design quality closets we provide quality leads!
Value Points:
Leads for closet companies are exclusive with a first right of refusal. Meaning, if the closet company cannot handle all of the leads we can provide, we will sell the excess to other closet companies. We will never sell the same lead to two different closet companies.
Benefits:
Flat rate and easy to budget
Cancel at anytime
Choose from 3 types of leads
Lower cost compared to overall cost per lead from other sources
More leads allows hiring more designers
More leads grow the companies revenue
Less time managing other advertising models
3 service options.
$250 each
- We send you the lead
- You and your team set the appointment
- Setting the appointment is up to you
2. $275 each
- We send you the lead
- We guarantee the appointment
- Return unset appointments for a replacement
3. $375 each
- We are your call center
- We generate the lead
- We set the appointment
Contact:
The Wardrobe Sage
704-555-0183
leads@TheWardrobeSage.com

```html
<!DOCTYPE html>
<html lang="en">
<head>
<meta charset="utf-8">
<title>The Wardrobe Sage – Lead Generation Pricing Flyer</title>
<link rel="stylesheet" href="https://fonts.googleapis.com/css2?family=Libre+Baskerville:wght@400;700&family=Great+Vibes&family=Poppins:wght@400;500&display=swap">
<style>
  :root {
    --brown: #a4612d;
    --brown-dark: #8a4f22;
    --black: #141210;
    --ink: #1d1b19;
    --paper: #ffffff;
    --line: #d9d4cf;
    --stage: #8e8e8e;
  }
  * { box-sizing: border-box; margin: 0; padding: 0; }
  html, body { width: 1200px; height: 2360px; overflow: hidden; }
  body { background: var(--stage); position: relative; font-family: "Poppins", sans-serif; color: var(--ink); }

  .flyer {
    position: absolute; left: 21px; top: 431px;
    width: 990px; height: 1280px;
    background: var(--paper);
    transform: scale(1.17); transform-origin: 0 0;
    overflow: hidden;
  }

  /* Header */
  .header-band { position: absolute; left: 0; top: 0; width: 990px; height: 330px; background: linear-gradient(90deg, #0d0c0b 0%, #221d19 60%, #1a1612 100%); }
  .header-accent { position: absolute; right: 0; top: 0; width: 113px; height: 330px; background: var(--brown); }
  .title { position: absolute; left: 58px; top: 55px; width: 400px; }
  .title-caps { font-family: "Libre Baskerville", serif; font-weight: 700; color: var(--brown); font-size: 45px; line-height: 44px; letter-spacing: 0.5px; }
  .title-script { font-family: "Great Vibes", cursive; color: #fff; font-size: 80px; line-height: 80px; margin-top: -6px; }
  .title-rule { height: 2px; background: var(--brown); width: 348px; margin-top: 2px; }
  .title-sub { font-family: "Libre Baskerville", serif; color: #fff; font-size: 29px; line-height: 34px; margin-top: 12px; }
  .title-sub strong { display: block; color: var(--brown); font-weight: 700; font-size: 29px; }

  .hero-photo { position: absolute; left: 465px; top: 58px; width: 470px; height: 373px; background: #fff; padding: 5px; }
  .hero-fill { width: 100%; height: 100%; background: linear-gradient(180deg, #d9cfc2 0%, #6b4330 45%, #3a2418 100%); }
  .hero-tag { position: absolute; left: 755px; top: 328px; width: 173px; height: 98px; background: rgba(164, 97, 45, 0.92); color: #fff; padding: 8px 12px; }
  .hero-tag small { font-family: "Libre Baskerville", serif; font-size: 11px; display: block; }
  .hero-tag span { font-family: "Great Vibes", cursive; font-size: 27px; line-height: 26px; display: block; margin-top: 2px; }

  /* Benefits */
  .benefits-bar { position: absolute; left: 0; top: 335px; width: 465px; height: 48px; background: var(--brown); }
  .benefits-bar h2 { font-family: "Libre Baskerville", serif; font-weight: 700; color: #fff; font-size: 27px; line-height: 48px; padding-left: 62px; }
  .benefit-list { position: absolute; left: 58px; top: 395px; width: 360px; list-style: none; }
  .benefit { position: relative; height: 70px; margin-bottom: 6px; }
  .benefit-box { position: absolute; left: 38px; top: 0; right: 0; height: 70px; border: 1.5px solid var(--line); border-left: none; border-radius: 0 8px 8px 0; display: flex; align-items: center; padding-left: 34px; font-size: 15px; line-height: 18px; }
  .benefit-icon { position: absolute; left: 0; top: 0; width: 70px; height: 70px; border-radius: 50%; border: 6px solid var(--black); border-right-color: var(--brown); border-bottom-color: var(--brown); background: #fff; display: flex; align-items: center; justify-content: center; }
  .benefit:nth-child(even) .benefit-icon { border-color: var(--brown); border-right-color: var(--black); border-bottom-color: var(--black); }
  .benefit-icon svg { width: 26px; height: 26px; }

  /* Values */
  .section-head { font-family: "Libre Baskerville", serif; font-weight: 700; font-size: 21px; color: var(--ink); display: flex; align-items: center; gap: 10px; }
  .section-head em { font-style: normal; color: var(--brown); }
  .section-head::after { content: ""; flex: 1; height: 1px; background: #999; }
  .values { position: absolute; left: 468px; top: 455px; width: 462px; }
  .values-grid { display: grid; grid-template-columns: 1fr 1fr; column-gap: 14px; row-gap: 8px; margin-top: 8px; list-style: none; font-size: 12.5px; line-height: 15px; }
  .values-grid li { position: relative; padding-left: 13px; }
  .values-grid li::before, .plan-points li::before { content: ""; position: absolute; left: 0; top: 4px; width: 7px; height: 7px; border-radius: 50%; border: 2px solid var(--brown); }

  /* Services */
  .services-head { position: absolute; left: 468px; top: 585px; width: 462px; font-family: "Libre Baskerville", serif; font-weight: 700; font-size: 21px; display: flex; align-items: center; gap: 12px; }
  .services-head::before, .services-head::after { content: ""; flex: 1; height: 1px; background: #999; }
  .services-head em { font-style: normal; color: var(--brown); }
  .plans { position: absolute; left: 468px; top: 625px; display: flex; gap: 18px; }
  .plan { position: relative; width: 142px; height: 305px; }
  .plan-number { position: absolute; left: 21px; top: 0; width: 100px; height: 50px; background: var(--black); border-radius: 50px 50px 0 0; color: #fff; text-align: center; font-family: "Libre Baskerville", serif; font-size: 15px; padding-top: 7px; }
  .plan-card { position: absolute; left: 0; top: 33px; width: 142px; height: 272px; background: var(--brown); border-radius: 12px; padding: 5px; }
  .plan-price { color: #fff; text-align: center; font-family: "Oswald", "Poppins", sans-serif; font-size: 42px; font-weight: 500; line-height: 48px; margin-top: 4px; letter-spacing: -1px; }
  .plan-price sup { font-size: 18px; vertical-align: 18px; }
  .plan-each { color: #fff; text-align: center; font-size: 13px; letter-spacing: 3px; line-height: 14px; }
  .plan-points { background: #fff; border-radius: 8px; margin-top: 9px; height: 182px; list-style: none; padding: 4px 8px; font-size: 11.5px; line-height: 13.5px; }
  .plan-points li { position: relative; padding: 4px 0 5px 14px; border-bottom: 1px solid #e4e0dc; }
  .plan-points li:last-child { border-bottom: none; }

  /* Gallery */
  .gallery { position: absolute; left: 58px; top: 950px; display: flex; gap: 12px; }
  .gallery-shot { width: 209px; height: 135px; border: 2px solid #cfcfcf; }
  .shot-office { background: linear-gradient(135deg, #d8d2c8, #2f3440 60%, #6d5a48); }
  .shot-wardrobe { background: linear-gradient(135deg, #f1eee9, #cfc6ba 55%, #8a7e70); }
  .shot-laundry { background: linear-gradient(135deg, #e2e3e5, #263149 55%, #bfc2c6); }
  .shot-living { background: linear-gradient(135deg, #efe9df, #5f5d5b 55%, #d8cdbd); }

  /* Contact */
  .brand-name { position: absolute; left: 58px; top: 1180px; width: 270px; font-family: "Libre Baskerville", serif; font-weight: 700; font-size: 24px; color: var(--brown); text-align: center; }
  .contact { position: absolute; left: 344px; top: 1140px; width: 590px; }
  .contact-head { font-family: "Libre Baskerville", serif; font-weight: 700; font-size: 32px; color: var(--black); display: flex; align-items: center; gap: 10px; }
  .contact-head em { font-style: normal; color: var(--brown); }
  .contact-head::after { content: ""; flex: 1; height: 1px; background: #999; margin-top: 12px; }
  .contact-lines { display: flex; gap: 38px; margin-top: 10px; font-family: "Libre Baskerville", serif; font-size: 24px; color: var(--ink); }
  .contact-lines span { display: flex; align-items: center; gap: 8px; }
  .contact-lines svg { width: 20px; height: 20px; }
</style>
</head>
<body>
<main class="flyer">
  <div class="header-band"></div>
  <div class="header-accent"></div>

  <header class="title">
    <div class="title-caps">A LEAD GENERATION</div>
    <div class="title-script">Service</div>
    <div class="title-rule"></div>
    <p class="title-sub">Exclusively for the <strong>custom closet industry</strong></p>
  </header>

  <div class="hero-photo"><div class="hero-fill" role="img" aria-label="Photo of a woman standing in a luxury walk-in closet with dark wood cabinetry and a chandelier"></div></div>
  <div class="hero-tag"><small>You design quality closets</small><span>We provide quality leads!</span></div>

  <div class="benefits-bar"><h2>Our benefits</h2></div>
  <ul class="benefit-list">
    <li class="benefit"><div class="benefit-box">Flat rate and easy to budget</div><div class="benefit-icon"><svg viewBox="0 0 24 24" fill="none" stroke="#555" stroke-width="2"><rect x="5" y="3" width="14" height="18" rx="1"/><path d="M8 8h8M8 12h8M8 16h5"/></svg></div></li>
    <li class="benefit"><div class="benefit-box">Cancel at anytime</div><div class="benefit-icon"><svg viewBox="0 0 24 24" fill="none" stroke="#555" stroke-width="2"><rect x="4" y="3" width="14" height="18" rx="1"/><path d="M7 17L19 5"/></svg></div></li>
    <li class="benefit"><div class="benefit-box">Choose from 3 types of leads</div><div class="benefit-icon"><svg viewBox="0 0 24 24" fill="none" stroke="#555" stroke-width="2"><circle cx="12" cy="9" r="3"/><circle cx="5" cy="14" r="2"/><circle cx="19" cy="14" r="2"/><path d="M7 21c1-4 9-4 10 0"/></svg></div></li>
    <li class="benefit"><div class="benefit-box">Lower cost compared to overall cost per lead from other sources</div><div class="benefit-icon"><svg viewBox="0 0 24 24" fill="none" stroke="#555" stroke-width="2"><circle cx="12" cy="9" r="6"/><path d="M12 15v6M9 18l3 3 3-3"/></svg></div></li>
    <li class="benefit"><div class="benefit-box">More leads allows hiring more designers</div><div class="benefit-icon"><svg viewBox="0 0 24 24" fill="none" stroke="#555" stroke-width="2"><circle cx="12" cy="7" r="3"/><path d="M6 21c0-6 12-6 12 0M3 10l3 2M21 10l-3 2"/></svg></div></li>
    <li class="benefit"><div class="benefit-box">More leads grow the companies revenue</div><div class="benefit-icon"><svg viewBox="0 0 24 24" fill="none" stroke="#555" stroke-width="2"><path d="M4 21h16M7 21v-6M12 21V9M17 21v-9M5 10l7-6 7 6"/></svg></div></li>
    <li class="benefit"><div class="benefit-box">Less time managing other advertising models</div><div class="benefit-icon"><svg viewBox="0 0 24 24" fill="none" stroke="#555" stroke-width="2"><path d="M6 3h12M6 21h12M7 3c0 6 10 6 10 9s-10 3-10 9M17 3c0 6-10 6-10 9"/></svg></div></li>
  </ul>

  <section class="values">
    <h2 class="section-head"><span>Our <em>values</em></span></h2>
    <ul class="values-grid">
      <li>Exclusive leads for closet companies</li>
      <li>Excess leads sold to other closet companies if unable to handle all</li>
      <li>First right of refusal principle applied</li>
      <li>Never sell the same lead to two different companies</li>
    </ul>
  </section>

  <h2 class="services-head"><span>Our <em>3 services</em></span></h2>
  <div class="plans">
    <article class="plan">
      <div class="plan-number">1</div>
      <div class="plan-card">
        <div class="plan-price"><sup>$</sup>250</div>
        <div class="plan-each">EACH</div>
        <ul class="plan-points">
          <li>We send you the lead</li>
          <li>You and your team set the appointment</li>
          <li>Setting the appointment is up to you</li>
        </ul>
      </div>
    </article>
    <article class="plan">
      <div class="plan-number">2</div>
      <div class="plan-card">
        <div class="plan-price"><sup>$</sup>275</div>
        <div class="plan-each">EACH</div>
        <ul class="plan-points">
          <li>We send you the lead</li>
          <li>You and your team set the appointment</li>
          <li>We guarantee the appointment</li>
          <li>Return unset appointments for a replacement</li>
        </ul>
      </div>
    </article>
    <article class="plan">
      <div class="plan-number">3</div>
      <div class="plan-card">
        <div class="plan-price"><sup>$</sup>375</div>
        <div class="plan-each">EACH</div>
        <ul class="plan-points">
          <li>We are your call center</li>
          <li>We generate the lead</li>
          <li>We set the appointment</li>
        </ul>
      </div>
    </article>
  </div>

  <div class="gallery">
    <div class="gallery-shot shot-office" role="img" aria-label="Home office with navy built-in cabinetry"></div>
    <div class="gallery-shot shot-wardrobe" role="img" aria-label="White walk-in wardrobe with open shelving"></div>
    <div class="gallery-shot shot-laundry" role="img" aria-label="Laundry room with navy cabinets and stacked washer and dryer"></div>
    <div class="gallery-shot shot-living" role="img" aria-label="Living room media wall with built-in shelves"></div>
  </div>

  <div class="brand-name">The Wardrobe Sage</div>

  <section class="contact">
    <h2 class="contact-head"><span>CONTACT <em>US</em></span></h2>
    <div class="contact-lines">
      <span><svg viewBox="0 0 24 24"><circle cx="12" cy="12" r="11" fill="#a4612d"/><path d="M8 6l2 3-1.5 1.5c.8 1.8 2.2 3.2 4 4L14 13l3 2-1 3c-5 0-10-5-10-10z" fill="#fff"/></svg>704-555-0183</span>
      <span><svg viewBox="0 0 24 24"><rect x="2" y="5" width="20" height="14" fill="#a4612d"/><path d="M2 5l10 8 10-8" fill="none" stroke="#fff" stroke-width="1.6"/></svg>leads@TheWardrobeSage.com</span>
    </div>
  </section>
</main>
</body>
</html>
```